Stylish Business Cards Wanted

- DOUBLE SIDED Design Required -

High end, edgy cards for a corporate and personal stylist. Must include logo,
Name: Belinda Harwick
Title: Director and Stylist
telephone : +61 8 7142 5809
email: belinda@theloombriefing.example
website: theloombriefing.example
Tag: Corporate Workwear & Uniform Specialist | Personal Stylist
Would like nice icons for telephone, email, website

Target Market(s)

Businesses wanting stylish uniforms, people wanting stylish wardrobes

Industry/Entity Type

Corporate Workwear Stylist

Contact Information for Business Card

I would like black, white and gold foiling incorporated in the design - possibly a touch of the other colours on my branding guide attached Name: Belinda Harwick Title: Director and Stylist telephone : +61 8 7142 5809 email: belinda@theloombriefing.example website: theloombriefing.example Tag: Corporate Workwear & Uniform Specialist | Personal Stylist Would like nice icons for telephone, email, website

Font styles to use
Other font styles liked:
• Raleway

Colors

Designer to choose colors to be used in the design.

Requirements
Must have
• Gold foil accents

```html
<!DOCTYPE html>
<html lang="en">
<head>
<meta charset="utf-8">
<title>The Loom Briefing – Business Cards</title>
<link href="https://fonts.googleapis.com/css2?family=Cinzel:wght@700&family=Open+Sans:wght@400;600&display=swap" rel="stylesheet">
<style>
  :root {
    --backdrop: #eeeeee;
    --card: #ffffff;
    --ink: #333333;
    --gold: #e0b64f;
  }
  * { margin: 0; padding: 0; box-sizing: border-box; }
  html, body { width: 1200px; height: 800px; overflow: hidden; }
  body {
    background: var(--backdrop);
    position: relative;
    font-family: "Open Sans", Arial, sans-serif;
    color: var(--ink);
  }
  .card {
    position: absolute;
    width: 572px;
    height: 331px;
    background: var(--card);
  }
  .card--contact { left: 475px; top: 32px; }
  .card--brand { left: 169px; top: 405px; }

  .holder { position: absolute; left: 35px; top: 52px; }
  .holder__name {
    font-family: "Cinzel", Georgia, serif;
    font-weight: 700;
    font-size: 19px;
    letter-spacing: 0.5px;
    color: var(--gold);
    line-height: 1;
  }
  .holder__title {
    font-size: 10px;
    color: var(--gold);
    margin-left: 4px;
    line-height: 1.2;
  }

  .tagline {
    position: absolute;
    left: 35px;
    top: 131px;
    font-size: 14px;
    line-height: 20px;
  }

  .contacts { position: absolute; left: 35px; top: 208px; list-style: none; }
  .contacts li {
    display: flex;
    align-items: center;
    height: 25px;
    font-size: 14px;
  }
  .contacts svg { width: 19px; height: 19px; margin-right: 9px; flex: none; }

  .wordmark {
    position: absolute;
    font-weight: 600;
    color: var(--ink);
    white-space: nowrap;
    transform: translate(-50%, -50%);
  }
  .card--contact .wordmark { left: 430px; top: 173px; font-size: 21px; }
  .card--brand .wordmark { left: 285px; top: 140px; font-size: 30px; }
</style>
</head>
<body>
  <section class="card card--contact">
    <div class="holder">
      <p class="holder__name">BELINDA HARWICK</p>
      <p class="holder__title">Director and Stylist</p>
    </div>
    <p class="tagline">
      Corporate Workwear &amp; Uniform Specialist<br>
      Personal Stylist
    </p>
    <ul class="contacts">
      <li>
        <svg viewBox="0 0 24 24" aria-hidden="true"><path fill="var(--gold)" d="M6.6 10.8c1.4 2.8 3.8 5.1 6.6 6.6l2.2-2.2c.3-.3.7-.4 1-.2 1.1.4 2.3.6 3.6.6.6 0 1 .4 1 1V20c0 .6-.4 1-1 1C10.6 21 3 13.4 3 4c0-.6.4-1 1-1h3.5c.6 0 1 .4 1 1 0 1.3.2 2.5.6 3.6.1.3 0 .7-.2 1L6.6 10.8z"/><path fill="none" stroke="var(--gold)" stroke-width="1.4" d="M14 3a7 7 0 0 1 7 7M14 6.5a3.5 3.5 0 0 1 3.5 3.5"/></svg>
        +61 8 7142 5809
      </li>
      <li>
        <svg viewBox="0 0 24 24" aria-hidden="true"><rect x="2" y="5" width="20" height="14" fill="var(--gold)"/><path d="M2 5l10 8 10-8M2 19l7-7M22 19l-7-7" fill="none" stroke="#fff" stroke-width="1.3"/></svg>
        belinda@theloombriefing.example
      </li>
      <li>
        <svg viewBox="0 0 24 24" aria-hidden="true"><g fill="none" stroke="var(--gold)" stroke-width="1.3"><circle cx="12" cy="12" r="10"/><ellipse cx="12" cy="12" rx="4.5" ry="10"/><path d="M2 12h20M4 6.5h16M4 17.5h16M12 2v20"/></g></svg>
        www.theloombriefing.example
      </li>
    </ul>
    <p class="wordmark">The Loom Briefing</p>
  </section>

  <section class="card card--brand">
    <p class="wordmark">The Loom Briefing</p>
  </section>
</body>
</html>
```